Flyer Design Project

I need a cool design that describes a new line of services I am selling. The final product should be a 8 1/2 by 11 and maximum two pages.

I am selling consulting services to learn to use web conferencing tools for business development, meeting and training.
Updates

Please use the file I have attached as a guide for your work. It is a document called "guide-quickofficehints" and I love its design.

Thanks

                                        Please substitute the new text availble and just uploaded in the FLYER. Please submit the FINAL version fo your design with TExt changes as well as improvements detailed in previous message. 

Target Market(s)

Entrepreneurs and classroom educators who wnats to explore a new way to teach (innovators not scared of technology)

Industry/Entity Type

Business

Requirements
Must have
• I would like to receive a final PDF with the content EDITABLE for minor edits (I have acrobat)
Logo should be included (attached)

PLEASE CHECK OUT ATTACHED DOCUMENT WHOSE DESIGN I LOVE.
IT is called "Guide quick-office hints". If you could follow that as a template to design mine that would be great!

```html
<!DOCTYPE html>
<html lang="en">
<head>
<meta charset="utf-8">
<title>Online Meeting Skills Services Flyer</title>
<link href="https://fonts.googleapis.com/css2?family=Arimo:ital,wght@0,400;0,700;1,400&display=swap" rel="stylesheet">
<style>
  :root {
    --canvas: #ffffff;
    --paper: #ffffff;
    --ink-dark: #111111;
    --brand-red: #b3261e;
    --brand-grey: #4a4a4a;
    --heading-blue: #3b55b6;
    --body-navy: #1f2a6b;
    --photo-deep: #1d2733;
    --photo-mid: #5d6c7c;
    --photo-light: #b9c4cf;
    --wave-soft: #e6ecf6;
    --wave-mid: #c9d5ea;
  }
  * { box-sizing: border-box; margin: 0; padding: 0; }
  html, body { width: 1200px; height: 900px; overflow: hidden; }
  body { background: var(--canvas); font-family: "Arimo", Arial, sans-serif; position: relative; }

  .page {
    position: absolute; top: 70px; width: 490px; height: 760px;
    background: var(--paper); overflow: hidden;
    box-shadow: 0 4px 14px rgba(0,0,0,0.25);
  }
  .page--cover { left: 90px; }
  .page--inside { left: 620px; }

  /* Cover */
  .brand { position: absolute; top: 46px; left: 0; width: 100%; text-align: center; }
  .brand__row { display: inline-flex; align-items: center; gap: 8px; }
  .brand__dot { width: 14px; height: 14px; border-radius: 50%; background: var(--brand-red); }
  .brand__name { font-size: 30px; font-weight: 700; color: var(--brand-grey); letter-spacing: 1px; }
  .brand__tagline { margin-top: 6px; font-size: 11px; color: var(--brand-grey); }

  .cover-photo {
    position: absolute; left: 0; top: 170px; width: 100%; height: 590px;
    background: linear-gradient(160deg, var(--photo-light) 0%, var(--photo-mid) 35%, var(--photo-deep) 75%, #0e141b 100%);
  }
  .cover-badge {
    position: absolute; left: -18px; top: 210px; width: 300px; height: 300px;
    border-radius: 50%; background: var(--ink-dark);
    display: flex; flex-direction: column; justify-content: center; align-items: center;
    text-align: center; color: #fff; padding: 0 28px 0 48px;
  }
  .cover-badge__title { font-size: 27px; line-height: 1.22; text-transform: uppercase; font-weight: 400; }
  .cover-badge__sub { font-size: 27px; line-height: 1.22; margin-top: 2px; }

  /* Inside */
  .inside-wave {
    position: absolute; inset: 0;
    background:
      radial-gradient(ellipse 420px 140px at 30% 28%, var(--wave-mid), transparent 70%),
      radial-gradient(ellipse 500px 160px at 70% 62%, var(--wave-mid), transparent 70%),
      linear-gradient(170deg, var(--wave-soft), #f7f9fd 55%, var(--wave-soft));
  }
  .inside-content { position: absolute; inset: 0; padding: 28px 32px 60px 30px; color: var(--body-navy); }
  .inside-heading { color: var(--heading-blue); font-size: 15px; font-weight: 700; line-height: 1.25; margin-bottom: 9px; }
  .inside-lead { font-size: 10.5px; font-weight: 700; margin-bottom: 7px; }
  .inside-text { font-size: 10.5px; line-height: 1.4; margin-bottom: 7px; }
  .inside-list { list-style: none; margin-bottom: 18px; }
  .inside-list li { font-size: 10.5px; line-height: 1.4; margin-bottom: 6px; padding-left: 10px; position: relative; }
  .inside-list li::before { content: "•"; position: absolute; left: 0; }
  .service-list li { margin-bottom: 8px; }
  .contact { position: absolute; left: 30px; bottom: 30px; color: var(--heading-blue); font-size: 12px; font-weight: 700; }
</style>
</head>
<body>

<section class="page page--cover">
  <header class="brand">
    <div class="brand__row">
      <span class="brand__dot"></span>
      <span class="brand__name">CONVENE CONSULTING</span>
    </div>
    <p class="brand__tagline">Learn. Connect. Grow.</p>
  </header>
  <div class="cover-photo" role="img" aria-label="Close-up photograph of a hand typing on a laptop keyboard in cool blue-grey light"></div>
  <div class="cover-badge">
    <h1 class="cover-badge__title">Online Meeting Skills Services:</h1>
    <p class="cover-badge__sub">It is just the beginning…</p>
  </div>
</section>

<section class="page page--inside">
  <div class="inside-wave" role="img" aria-label="Soft abstract blue wave background"></div>
  <div class="inside-content">
    <h2 class="inside-heading">What if your business can reach all the people already interested in learning what you know?</h2>
    <p class="inside-lead">A different use of webinar technology: the first step towards a new way of thinking about your market and clients.</p>
    <p class="inside-text">You probably know about webinars. You have attended a few and found them boring and one-sided, with no chance to ask questions. The good news: it does not have to be that way. We help you design live sessions that invite people in, keep them talking and bring them back.</p>
    <ul class="inside-list">
      <li>We design an effective virtual meeting experience for you using the tools of the online room to their full potential.</li>
      <li>We coach you and your team to plan, host and follow up on sessions that turn attendees into clients.</li>
      <li>We help you launch your first webinar with a live audience and review the results together.</li>
    </ul>

    <h2 class="inside-heading">Choose the service that best fit your needs and budget. A new level of online engagement and virtual collaboration awaits.</h2>
    <ul class="inside-list service-list">
      <li>“Webinar Series”: Plan, design, develop and implement a four-session webinar series about your content, hosted on our platform ($3,500).</li>
      <li>“Webinar”: Plan, design, develop and implement one webinar session with coaching for your presenters ($1,200).</li>
      <li>“Outfitting the Online Entrepreneur”: Five hours of one-on-one coaching to learn online tools and build your first virtual event ($1,000).</li>
      <li>“Repurposing for online audiences”: Design and develop materials and lesson plans to adapt your face-to-face content ($800).</li>
      <li>“One-to-one coaching”: Three hours of coaching on online tools and session planning ($500).</li>
      <li>“One-on-one coaching”: One hour to learn the basics of hosting online meetings ($200).</li>
    </ul>

    <h2 class="inside-heading">You'll participate via the CloudRoom Meeting platform. No special software is required. If you have a computer with Internet access and a direct telephone line you have all is needed to participate.</h2>
    <p class="inside-text">As a small business owner, you know that web technology is here to stay. Now is the time to use it well. Let us help you reach new markets and grow your business at minimum cost.</p>
  </div>
  <p class="contact">For more information, give us a call at 555-0142-2371.</p>
</section>

</body>
</html>
```